Law Firm Business Card

This is a business card for a law firm that serves US military and veterans.

The card must have ONLY the following (we want an uncluttered look):

- Company logo (PNG, GIF, JPEG copies uploaded)
- A tagline reading: "a law firm for service members and veterans"
- My name and title: "Tobias Marlow" and "Attorney"
- My email: "tobias.marlow@brinmoorlegal.com"
- My number: "855-FIRM-ONE (347-6663)"

We are looking for a clean, simple layout with only the above information, likely printed on a bright white cotton stock. The font of our logo is DIN 1451, and the font used on our website is Helvetica Neue. The color of our logo is #336699, and we probably want the tagline in that color also, and my contact information in a dark grey. Please review our website at www.brinmoorlegal.com to ensure your card design complements our website style.

Thanks and we look forward to seeing your submissions.

A few notes:

- Two-sided submissions are ok
- Please don't add graphics (scales of justice, judges hammer, etc)

```html
<!DOCTYPE html>
<html lang="en">
<head>
<meta charset="utf-8">
<title>Brinmoor Legal – Business Card</title>
<link rel="stylesheet" href="https://fonts.googleapis.com/css2?family=Barlow+Semi+Condensed:wght@500;600&family=Barlow:wght@400;500&display=swap">
<style>
  :root {
    --brand-blue: #336699;
    --card-white: #ffffff;
    --ink-dark: #333333;
    --ink-black: #111111;
    --stage: #e9e6e2;
    --edge: rgba(0,0,0,0.18);
  }
  * { box-sizing: border-box; margin: 0; padding: 0; }
  html, body {
    width: 1200px;
    height: 952px;
    overflow: hidden;
    background: var(--stage);
  }
  .stage {
    position: relative;
    width: 1200px;
    height: 952px;
  }
  .card {
    position: absolute;
    width: 660px;
    height: 380px;
    box-shadow: 0 2px 10px var(--edge);
    overflow: hidden;
  }
  .card--front {
    left: 90px;
    top: 70px;
    background: var(--card-white);
  }
  .card--back {
    left: 450px;
    top: 500px;
    background: var(--brand-blue);
    display: flex;
    align-items: center;
    justify-content: center;
  }

  .wordmark {
    font-family: "Barlow Semi Condensed", "Arial Narrow", sans-serif;
    font-weight: 600;
    text-transform: uppercase;
    letter-spacing: 1px;
    line-height: 1;
    white-space: nowrap;
  }
  .card--front .wordmark {
    position: absolute;
    top: 70px;
    left: 0;
    width: 100%;
    text-align: center;
    font-size: 64px;
    color: var(--brand-blue);
  }
  .card--back .wordmark {
    font-size: 84px;
    color: var(--card-white);
  }

  .tagline {
    position: absolute;
    top: 168px;
    left: 0;
    width: 100%;
    text-align: center;
    font-family: "Barlow Semi Condensed", "Arial Narrow", sans-serif;
    font-weight: 500;
    font-size: 23px;
    letter-spacing: 0.5px;
    color: var(--brand-blue);
  }

  .signature {
    position: absolute;
    right: 28px;
    top: 238px;
    text-align: right;
  }
  .signature__name {
    font-family: "Barlow Semi Condensed", "Arial Narrow", sans-serif;
    font-weight: 600;
    font-size: 24px;
    color: var(--brand-blue);
    line-height: 1.1;
  }
  .signature__title {
    font-family: "Barlow", Helvetica, sans-serif;
    font-size: 15px;
    color: var(--ink-black);
  }
  .tab {
    position: absolute;
    width: 6px;
    background: var(--brand-blue);
  }
  .tab--right { right: 0; top: 232px; height: 56px; }
  .tab--left { left: 0; top: 292px; height: 76px; }

  .contact {
    position: absolute;
    left: 24px;
    top: 296px;
    list-style: none;
    font-family: "Barlow", Helvetica, sans-serif;
    font-size: 17px;
    color: var(--ink-dark);
  }
  .contact__item {
    display: flex;
    align-items: center;
    gap: 10px;
    height: 25px;
  }
  .contact__icon {
    width: 16px;
    height: 16px;
    flex: none;
    fill: var(--brand-blue);
  }
</style>
</head>
<body>
<main class="stage">

  <section class="card card--front" aria-label="Business card front">
    <div class="wordmark">Brinmoor Legal</div>
    <p class="tagline">A Law Firm For Service Members &amp; Veterans</p>

    <span class="tab tab--right"></span>
    <div class="signature">
      <p class="signature__name">Tobias Marlow</p>
      <p class="signature__title">Attorney</p>
    </div>

    <span class="tab tab--left"></span>
    <ul class="contact">
      <li class="contact__item">
        <svg class="contact__icon" viewBox="0 0 16 16" aria-hidden="true">
          <circle cx="8" cy="8" r="7.5" fill="none" stroke="#336699" stroke-width="1"/>
          <path d="M5 4.2c.4-.3.9-.2 1.1.2l.7 1.3c.2.4 0 .8-.3 1l-.4.3c.4.9 1.1 1.7 2 2.2l.3-.4c.3-.3.7-.4 1-.2l1.3.8c.4.2.5.7.2 1.1l-.5.6c-.4.4-1 .6-1.6.3C6.9 10.6 5.4 9 4.6 7.1c-.2-.6 0-1.2.4-1.6z"/>
        </svg>
        855-FIRM-ONE (347-6663)
      </li>
      <li class="contact__item">
        <svg class="contact__icon" viewBox="0 0 16 16" aria-hidden="true">
          <path d="M1 4h14v9H1z"/>
          <path d="M1 4l7 5 7-5" fill="none" stroke="#ffffff" stroke-width="1.2"/>
        </svg>
        tobias.marlow@brinmoorlegal.com
      </li>
      <li class="contact__item">
        <svg class="contact__icon" viewBox="0 0 16 16" aria-hidden="true">
          <circle cx="8" cy="8" r="7"/>
          <g fill="none" stroke="#ffffff" stroke-width="0.9">
            <ellipse cx="8" cy="8" rx="3" ry="7"/>
            <path d="M1 8h14M2.2 4.5h11.6M2.2 11.5h11.6"/>
          </g>
        </svg>
        www.brinmoorlegal.com
      </li>
    </ul>
  </section>

  <section class="card card--back" aria-label="Business card back">
    <div class="wordmark">Brinmoor Legal</div>
  </section>

</main>
</body>
</html>
```